Preschool Website

Looking to have a one page splash with a contact us form that uses some kind of verification to keep bots from filling out the form. We would like for it to be dynamic for both mobile and desktop. Would like to have it show up in search engines for preschool in are area. Would like to include a link to the website are current parents use for payment information.

Target Market(s)

Young Adults with Childrens

Industry/Entity Type

Preschool

Coding

Coded - Design and coding required

Number of Pages Required

1 page

Colors

Designer to choose colors to be used in the design.

Requirements
Must have
• Searchable in Quorla
• Contact us form
• Name
• Phone
• Email
• Message box
• Form must have code entered to submit to prevent junk emails
• Link to the website we use for parents to make payments
• our phone and address clickable on device to make call or map on phone
Should not have
• more then one page

```html
<!DOCTYPE html>
<html lang="en">
<head>
<meta charset="utf-8">
<title>Brightleaf Preschool</title>
<meta name="viewport" content="width=1200">
<link rel="stylesheet" href="https://fonts.googleapis.com/css2?family=Dosis:wght@400;500;600;700&family=Open+Sans:wght@400;600;700&family=Oswald:wght@400;500&display=swap">
<style>
:root{
  --orange:#ffa82a;
  --orange-dark:#f7901e;
  --blue:#2f6cff;
  --blue-deep:#2458e6;
  --purple:#a25cff;
  --magenta:#e66bff;
  --yellow:#ffd50f;
  --pink:#f2506b;
  --coral:#ff7a6a;
  --ink:#333a45;
  --muted:#8b919b;
  --line:#e6e8ee;
  --white:#ffffff;
}
*{box-sizing:border-box;margin:0;padding:0}
html,body{width:1200px;height:4312px;overflow:hidden}
body{position:relative;font-family:"Open Sans",sans-serif;color:var(--ink);background:var(--white)}
h1,h2,h3,h4{font-family:"Dosis",sans-serif;font-weight:600}
.ph{border-radius:14px}

/* header / hero */
.hero{position:absolute;left:0;top:0;width:1200px;height:700px}
.hero svg.bg{position:absolute;left:0;top:0}
.brand{position:absolute;display:flex;align-items:center;gap:10px;font-family:"Dosis",sans-serif;font-weight:700;font-size:26px;color:var(--white)}
.brand .dot{width:26px;height:26px;border-radius:50%;background:var(--white)}
.hero .brand{left:40px;top:28px}
.topbar-icon{position:absolute;left:1030px;top:30px;width:34px;height:34px;border-radius:50%;border:2px solid var(--white)}
.phone-pill{position:absolute;left:1080px;top:30px;width:90px;height:34px;border-radius:17px;background:var(--blue);color:var(--white);font-size:11px;font-weight:700;display:flex;align-items:center;justify-content:center;text-decoration:none}
.hero-title{position:absolute;left:40px;top:170px;width:400px;color:var(--white);font-size:38px;line-height:1.2;font-weight:700}
.hero-text{position:absolute;left:40px;top:285px;width:420px;color:var(--white);font-size:15px;line-height:1.6}
.btn{display:inline-flex;align-items:center;justify-content:center;border-radius:22px;font-family:"Dosis",sans-serif;font-weight:600;font-size:15px}
.hero .btn{position:absolute;left:40px;top:420px;width:130px;height:40px;background:var(--blue);color:var(--white)}
.hero-photo{position:absolute;left:560px;top:80px;width:600px;height:540px;border-radius:48% 52% 46% 54% / 50% 46% 54% 50%;background:linear-gradient(135deg,#f4c99c,#e9a46a 45%,#7fb6e8)}
.play{position:absolute;left:820px;top:300px;width:64px;height:64px;border-radius:50%;background:var(--blue);display:flex;align-items:center;justify-content:center}

/* section titles */
.sec-title{position:absolute;left:0;width:1200px;text-align:center;font-size:40px;font-weight:500;color:var(--ink)}

/* programs */
.programs{position:absolute;left:90px;top:920px;display:flex;gap:32px}
.program{width:228px;height:240px;border-radius:12px;background:var(--white);box-shadow:0 6px 24px rgba(40,60,110,.12);padding:24px 20px}
.icon-ring{width:52px;height:52px;border-radius:50%;border:2px solid var(--blue);display:flex;align-items:center;justify-content:center;margin-bottom:14px}
.program h3{font-size:22px;font-weight:500}
.program .age{font-size:12px;color:var(--muted);margin:2px 0 10px}
.program p{font-size:13px;line-height:1.55;color:var(--muted)}

/* cta */
.cta{position:absolute;left:0;top:1212px;width:1200px;height:108px;background:linear-gradient(90deg,var(--purple),var(--magenta))}
.cta h2{position:absolute;left:130px;top:30px;font-size:38px;font-weight:500;color:var(--white)}
.cta h2 span{color:var(--yellow)}
.cta .btn{position:absolute;left:900px;top:32px;width:190px;height:44px;background:var(--yellow);color:var(--ink)}

/* values */
.values{position:absolute;left:130px;top:1430px;display:grid;grid-template-columns:500px 440px;row-gap:40px}
.value{display:flex;gap:22px}
.value .ph{width:100px;height:100px;flex:none}
.value h3{font-size:24px;font-weight:500;margin:6px 0 8px}
.value p{font-size:13px;line-height:1.6;color:var(--muted);width:300px}

/* events */
.events-bg{position:absolute;left:0;top:1700px}
.events-title{color:var(--white)}
.events{position:absolute;left:130px;top:1940px;display:grid;grid-template-columns:500px 460px;row-gap:40px}
.event{display:flex;gap:24px}
.event .ph{width:200px;height:150px;flex:none;border-radius:16px}
.tag{display:inline-block;background:var(--orange);color:var(--white);font-size:10px;font-weight:700;padding:4px 10px;border-radius:3px}
.event h3{color:var(--white);font-size:24px;line-height:1.15;margin:8px 0}
.event p{color:#dce6ff;font-size:13px;line-height:1.55;width:230px}

/* classes */
.classes{position:absolute;left:140px;top:2672px;display:flex;gap:30px}
.class-card{width:300px;height:290px;border-radius:10px;background:var(--white);box-shadow:0 6px 22px rgba(40,60,110,.12);overflow:hidden}
.class-card .ph{height:150px;border-radius:0}
.class-card h3{color:var(--blue);font-size:22px;font-weight:600;padding:12px 18px 4px}
.class-card p{font-size:12px;line-height:1.5;color:var(--muted);padding:0 18px}
.stats{display:flex;justify-content:space-between;padding:12px 28px 0;text-align:center}
.stats b{display:block;font-size:11px;color:var(--ink);font-weight:600}
.stats span{font-size:11px;color:var(--orange)}
.dots{position:absolute;left:588px;display:flex;gap:8px}
.dots i{width:8px;height:8px;border-radius:50%;background:#cfd6e6}
.dots i.on{background:var(--blue)}

/* parents */
.parents{position:absolute;left:140px;top:3160px;display:flex;gap:70px}
.parent{width:440px;display:flex;gap:20px}
.avatar{width:80px;height:80px;border-radius:50%;flex:none;background:linear-gradient(135deg,#caa07c,#7b5a48)}
.parent h3{font-size:22px;font-weight:500;margin:6px 0 10px}
.parent p{font-size:13px;line-height:1.6;color:var(--muted)}

/* contact */
.contact{position:absolute;left:0;top:3392px;width:1200px;height:400px;background:linear-gradient(90deg,var(--pink),var(--coral))}
.form-card{position:absolute;left:32px;top:28px;width:270px;height:346px;background:var(--white);border-radius:6px;padding:16px 18px}
.form-card h4{font-size:16px;margin-bottom:2px}
.form-card small{font-size:9px;color:var(--muted);display:block;margin-bottom:8px}
.field{height:22px;border:1px solid var(--line);border-radius:3px;margin-bottom:8px;font-size:9px;color:var(--muted);padding:4px 6px}
.field.msg{height:60px}
.captcha{display:flex;gap:8px;margin-bottom:8px}
.captcha .code{width:80px;height:24px;background:#eef1f6;font-family:"Oswald",sans-serif;font-size:13px;letter-spacing:3px;text-align:center;line-height:24px}
.captcha .field{flex:1;margin:0}
.form-card .send{width:64px;height:22px;border-radius:3px;background:var(--blue);color:var(--white);font-size:10px;display:flex;align-items:center;justify-content:center}
.map{position:absolute;left:340px;top:28px;width:420px;height:346px;border-radius:4px;background:linear-gradient(135deg,#eef0e8,#dfe5dc 50%,#cfd9e6)}
.info{position:absolute;left:830px;top:80px;font-family:"Oswald",sans-serif;color:var(--white);font-size:22px;line-height:1.55;text-transform:uppercase}
.info p{margin-bottom:16px}
.info a{color:var(--white);text-decoration:none}

/* signup */
.signup{position:absolute;left:80px;top:3840px;width:1040px;height:250px;border-radius:18px;background:var(--blue);text-align:center;color:var(--white)}
.signup h2{font-size:44px;font-weight:500;margin-top:36px}
.signup p{font-size:13px;color:#dfe7ff;width:560px;margin:12px auto 0;line-height:1.6}
.subscribe{position:absolute;left:290px;top:168px;width:460px;height:44px;border-radius:22px;background:var(--blue-deep);border:1px solid rgba(255,255,255,.35);display:flex;align-items:center;padding-left:22px;font-size:13px;color:#c7d5ff}
.subscribe .btn{position:absolute;right:0;top:-1px;width:120px;height:44px;background:var(--orange);color:var(--white)}

/* footer */
.footer .brand{left:140px;top:4140px;color:var(--orange)}
.footer .brand .dot{background:var(--orange)}
.foot-text{position:absolute;left:140px;top:4190px;width:220px;font-size:12px;line-height:1.6;color:var(--muted)}
.foot-col{position:absolute;top:4140px;font-size:12px;color:var(--muted);line-height:1.8}
.foot-col h4{font-family:"Open Sans",sans-serif;font-size:12px;font-weight:700;color:var(--ink);text-transform:uppercase;margin-bottom:4px}
.foot-col a{color:var(--muted);text-decoration:none}
.two{display:flex;gap:40px}
</style>
</head>
<body>

<header class="hero">
  <svg class="bg" width="1200" height="700" viewBox="0 0 1200 700" aria-hidden="true">
    <path d="M0 0H1200V600C1080 660 960 690 820 650C680 610 560 560 420 610C290 656 160 690 0 640Z" fill="var(--orange)"/>
  </svg>
  <div class="brand"><span class="dot"></span>brightleaf</div>
  <div class="topbar-icon"></div>
  <a class="phone-pill" href="tel:5550142277">(555) 014-2277</a>
  <h1 class="hero-title">When should I begin to look at schools?</h1>
  <p class="hero-text">A helpful guide to the application, visiting and enrollment process for public and private schools in the city of Fernwood.</p>
  <a class="btn">Learn more</a>
  <div class="hero-photo" role="img" aria-label="Photo of a teacher with young children at a classroom table"></div>
  <div class="play"><svg width="22" height="22" viewBox="0 0 22 22"><path d="M7 4L18 11L7 18Z" fill="#fff"/></svg></div>
</header>

<h2 class="sec-title" style="top:820px">Brightleaf Programs</h2>
<section class="programs">
  <div class="program"><div class="icon-ring"><svg width="24" height="24"><circle cx="12" cy="12" r="8" fill="none" stroke="#2f6cff" stroke-width="2"/></svg></div><h3>Toddler</h3><div class="age">(1.5 - 3 years)</div><p>By creating a safe, consistent and welcoming environment, we help</p></div>
  <div class="program"><div class="icon-ring"><svg width="24" height="24"><rect x="5" y="5" width="14" height="14" rx="2" fill="none" stroke="#2f6cff" stroke-width="2"/></svg></div><h3>Preschool</h3><div class="age">(2 - 5 years)</div><p>Well balanced days with directed play and thoughtful lessons</p></div>
  <div class="program"><div class="icon-ring"><svg width="24" height="24"><path d="M4 18L12 5L20 18Z" fill="none" stroke="#2f6cff" stroke-width="2"/></svg></div><h3>Kindergarten</h3><div class="age">(5 - 6 years)</div><p>A small class size and exceptional teachers enable children to offer</p></div>
  <div class="program"><div class="icon-ring"><svg width="24" height="24"><path d="M12 4L14 10H20L15 14L17 20L12 16L7 20L9 14L4 10H10Z" fill="none" stroke="#2f6cff" stroke-width="2"/></svg></div><h3>Pre-K Program</h3><div class="age">(4 - 5 years)</div><p>Our school follows the guidelines of the local school district in order to</p></div>
</section>

<section class="cta">
  <h2>Apply for <span>Admission</span> Call to Action</h2>
  <a class="btn">Learn more</a>
</section>

<h2 class="sec-title" style="top:1350px">Our core values</h2>
<section class="values">
  <div class="value"><div class="ph" role="img" aria-label="Photo of children learning and playing" style="background:linear-gradient(135deg,#f3c08a,#9ac4e8)"></div><div><h3>Learning &amp; Fun</h3><p>Happy days start with curious minds, caring teachers and bright rooms.</p></div></div>
  <div class="value"><div class="ph" role="img" aria-label="Photo of a healthy children's meal" style="background:linear-gradient(135deg,#b8d98a,#f2a66a)"></div><div><h3>Healthy Meals</h3><p>Fresh snacks and balanced lunches are prepared daily in our kitchen.</p></div></div>
  <div class="value"><div class="ph" role="img" aria-label="Photo of children playing safely outdoors" style="background:linear-gradient(135deg,#a7d38c,#e9c49a)"></div><div><h3>Children Safety</h3><p>Secure entrances and attentive staff keep every little one protected.</p></div></div>
  <div class="value"><div class="ph" role="img" aria-label="Photo of a cheerful classroom" style="background:linear-gradient(135deg,#f6d28e,#8fc0ea)"></div><div><h3>Cute Environment</h3><p>Colourful, cozy spaces invite children to explore and create freely.</p></div></div>
</section>

<svg class="events-bg" width="1200" height="760" viewBox="0 0 1200 760" aria-hidden="true">
  <path d="M0 60C150 10 300 0 460 40C640 86 800 90 980 40C1060 18 1130 20 1200 40V700C1040 740 880 760 700 720C520 680 360 700 200 740C120 756 60 752 0 740Z" fill="var(--blue)"/>
</svg>
<h2 class="sec-title events-title" style="top:1840px">Events</h2>
<section class="events">
  <div class="event"><div class="ph" role="img" aria-label="Photo of children at a family event" style="background:linear-gradient(135deg,#f4b98a,#6fa0f0)"></div><div><span class="tag">10 am - 6 pm</span><h3>Father's Day Sundaes &amp; Shaving!</h3><p>Decorate and celebrate with dads, treats and silly foam fun.</p></div></div>
  <div class="event"><div class="ph" role="img" aria-label="Photo of children in costumes" style="background:linear-gradient(135deg,#f0c89c,#8cb8f2)"></div><div><span class="tag">9 am - 2 pm</span><h3>Halloween Bash Lorem Ipsum</h3><p>Costumes, pumpkins and games for the whole family on Friday.</p></div></div>
  <div class="event"><div class="ph" role="img" aria-label="Photo of children with a balloon" style="background:linear-gradient(135deg,#9fd07a,#f0b66e)"></div><div><span class="tag">11 am - 4 pm</span><h3>Last Day of School and of Year Picnic</h3><p>Games, music and lunch on the lawn to close the school year.</p></div></div>
  <div class="event"><div class="ph" role="img" aria-label="Photo of children playing on a slide" style="background:linear-gradient(135deg,#f5d08a,#7fb0ee)"></div><div><span class="tag">11 am - 4 pm</span><h3>Last Day of School and of Year Picnic</h3><p>Join us outside to celebrate growth, friendship and creativity.</p></div></div>
</section>

<h2 class="sec-title" style="top:2530px">Classes</h2>
<section class="classes">
  <div class="class-card"><div class="ph" role="img" aria-label="Photo of colourful toy blocks" style="background:linear-gradient(135deg,#ffd36a,#ef7a5a 50%,#6aa6f0)"></div><h3>Color Matching Class</h3><p>A playful class for children to learn colors with shapes and toys.</p><div class="stats"><div><b>Age</b><span>3-4 yrs</span></div><div><b>Size</b><span>12 kids</span></div><div><b>Price</b><span>$20/hr</span></div></div></div>
  <div class="class-card"><div class="ph" role="img" aria-label="Photo of a child learning letters" style="background:linear-gradient(135deg,#f7c79a,#9cc6ee)"></div><h3>Alphabet Matching Class</h3><p>Early readers match letters and sounds through games and songs.</p><div class="stats"><div><b>Age</b><span>4-5 yrs</span></div><div><b>Size</b><span>10 kids</span></div><div><b>Price</b><span>$22/hr</span></div></div></div>
  <div class="class-card"><div class="ph" role="img" aria-label="Photo of children with letter cards" style="background:linear-gradient(135deg,#f1d5b8,#b7d2ee)"></div><h3>Letter Match Class</h3><p>Hands-on letter practice that builds early writing confidence.</p><div class="stats"><div><b>Age</b><span>5-6 yrs</span></div><div><b>Size</b><span>10 kids</span></div><div><b>Price</b><span>$22/hr</span></div></div></div>
</section>
<div class="dots" style="top:2990px"><i class="on"></i><i></i></div>

<h2 class="sec-title" style="top:3050px">Our happy parents</h2>
<section class="parents">
  <div class="parent"><div class="avatar" role="img" aria-label="Portrait of a parent"></div><div><h3>Elena Marwick</h3><p>We decided to seriously cooperate with Brightleaf because of their quality services, including because of their on-the-job training program and other incentives for students to help reduce learning time.</p></div></div>
  <div class="parent"><div class="avatar" role="img" aria-label="Portrait of a parent"></div><div><h3>Tessa Hollin</h3><p>Brightleaf Preschool is a great place for my daughter to start her schooling experience. It's welcoming and safe and my daughter loves being there. Her skill level is significantly better since attending.</p></div></div>
</section>
<div class="dots" style="top:3350px"><i class="on"></i><i></i></div>

<section class="contact">
  <div class="form-card">
    <h4>Get in Touch</h4>
    <small>We reply to every message within one day.</small>
    <div class="field">Name</div>
    <div class="field">Phone</div>
    <div class="field">Email</div>
    <div class="field msg">Message</div>
    <div class="captcha"><div class="code">7K4QP</div><div class="field">Enter code</div></div>
    <small>Enter the code shown above to send your message.</small>
    <div class="send">Submit</div>
  </div>
  <div class="map" role="img" aria-label="Street map showing the school location"></div>
  <div class="info">
    <p>Name: Preschool</p>
    <p><a href="tel:+15550183390">Phone: +1 555 018 3390</a></p>
    <p>Email: hello@brightleaf.test</p>
    <p>Address: 12 Maple Lantern Lane,<br>Fernwood Country</p>
  </div>
</section>

<section class="signup">
  <h2>Sign up for open day</h2>
  <p>Come see our classrooms, meet our teachers and explore the programs we offer for your little ones this season.</p>
  <div class="subscribe">Your E-mail <span class="btn">Submit →</span></div>
</section>

<footer class="footer">
  <div class="brand"><span class="dot"></span>brightleaf</div>
  <p class="foot-text">Early years for curious kids, with care and play every day in Fernwood.</p>
  <div class="foot-col" style="left:380px"><h4>Contact Info</h4>12 Maple Lantern Lane<br><a href="tel:+15550183390">+1 555 018 3390</a><br>hello@brightleaf.test</div>
  <div class="foot-col" style="left:630px"><h4>Quick Links</h4>Home<br>About Us<br>Programs</div>
  <div class="foot-col" style="left:880px"><h4>Information For</h4><div class="two"><div>Parents<br>Gallery<br>Events</div><div>FAQ<br><a>Pay Tuition</a><br>Contact</div></div></div>
</footer>

</body>
</html>
```